Finiding oppertunites in Real Estate 6.15.20

size of ad 7” x 9.6”
1-I like the ad to stand out and attract people's attention.
2-you should be able to see the text of the ad clearly .. see the attachment anything in yellow is instructions.
3-the list of topics should not be the main part of the ad
4-if you decide you want a picture or vector of a person .. (you decide)
then it should be a white male about 25-30 years old wearing a solid white or blue shirt and not long hair.
5-leave 1 inch for footer
see attachment
Good luck

Target Market(s)

potential male students 25-35 years of age

Industry/Entity Type

Education

Requirements
Must have
• will stand out and people would want to see it.
should be able to read the words of ad
Nice to have
• how to make money in real estate on one line

```html
<!DOCTYPE html>
<html lang="en">
<head>
<meta charset="utf-8">
<title>Real Estate Career Course</title>
<link rel="stylesheet" href="https://fonts.googleapis.com/css2?family=Nunito:wght@800;900&family=Nunito+Sans:ital,wght@0,300;0,400;0,600;0,800;0,900;1,900&display=swap">
<style>
  :root {
    --royal: #16359a;
    --gold: #c2b06b;
    --olive-gold: #aa9a3a;
    --navy-top: #2d3b68;
    --navy-bottom: #111c3b;
    --cream: #efe9d9;
    --ink: #1d1d1d;
    --white: #ffffff;
  }
  * { margin: 0; padding: 0; box-sizing: border-box; }
  html, body { width: 832px; height: 1200px; overflow: hidden; background: var(--white); }
  .flyer {
    position: relative; width: 832px; height: 1200px; overflow: hidden;
    font-family: "Nunito Sans", sans-serif; color: var(--ink);
    background: linear-gradient(to bottom, var(--white) 0, var(--white) 720px, var(--cream) 830px, var(--cream) 1056px, var(--white) 1056px);
  }
  .abs { position: absolute; }
  .title {
    top: 46px; left: 0; width: 832px; text-align: center;
    font-family: "Nunito", sans-serif; font-weight: 900; color: var(--royal);
    font-size: 62px; line-height: 56px; letter-spacing: 1px;
  }
  .tagline {
    background: var(--gold); color: var(--ink); font-size: 23px; line-height: 40px;
    text-align: center; white-space: nowrap;
  }
  .tag-1 { left: 210px; top: 183px; width: 412px; }
  .tag-2 { left: 57px; top: 235px; width: 718px; }
  .tag-3 { left: 72px; top: 287px; width: 687px; }
  .houses-photo {
    left: 0; top: 360px; width: 832px; height: 162px;
    background: radial-gradient(ellipse at 46% 70%, #d23a3a 0 5%, transparent 9%),
                linear-gradient(to bottom, #f4f6f6, #d9dee0 55%, #f7f8f8);
  }
  .promo-panel {
    left: 40px; top: 541px; width: 753px; height: 262px;
    background: linear-gradient(to bottom, var(--navy-top), var(--navy-bottom) 45%);
  }
  .remote-illustration {
    left: 70px; top: 575px; width: 270px; height: 98px;
    background: linear-gradient(135deg, #e9a23a, #d85a2a 60%, #8fb6dc);
    border-radius: 4px;
  }
  .remote {
    left: 68px; top: 664px; font-family: "Nunito", sans-serif; font-weight: 900;
    font-size: 66px; line-height: 60px; color: var(--olive-gold); letter-spacing: 0.5px;
  }
  .sessions {
    left: 66px; top: 713px; font-weight: 300; font-size: 66px; line-height: 62px;
    color: var(--white); letter-spacing: 1px;
  }
  .divider { left: 414px; top: 563px; width: 3px; height: 221px; background: var(--olive-gold); }
  .count {
    left: 452px; top: 578px; font-family: "Nunito", sans-serif; font-weight: 900;
    font-size: 106px; line-height: 106px; color: var(--olive-gold); letter-spacing: -4px;
  }
  .count-unit {
    left: 562px; top: 578px; font-family: "Nunito", sans-serif; font-weight: 900;
    font-size: 58px; line-height: 44px; color: var(--white);
  }
  .start-date {
    left: 452px; top: 676px; width: 316px; text-align: center; font-weight: 300;
    font-size: 44px; line-height: 44px; color: var(--white);
  }
  .topics-heading {
    left: 0; top: 836px; width: 812px; text-align: center; font-weight: 800;
    font-size: 30px; color: var(--ink);
  }
  .topic-list { list-style: none; }
  .topic {
    position: absolute; display: flex; align-items: center; gap: 12px;
    font-size: 15.5px; letter-spacing: 0.4px; color: var(--ink); white-space: nowrap;
  }
  .topic svg { width: 18px; height: 18px; flex: none; }
  .company { left: 39px; top: 1092px; font-size: 15px; line-height: 19px; }
  .company .name { color: var(--gold); }
  .contact { left: 280px; top: 1092px; font-size: 15px; line-height: 21px; }
  .contact li { list-style: none; display: flex; align-items: center; gap: 10px; }
  .contact svg { width: 15px; height: 13px; flex: none; }
  .hotline { right: 42px; top: 1096px; text-align: right; }
  .hotline .label { font-weight: 900; font-size: 25px; line-height: 25px; color: var(--olive-gold); }
  .hotline .number { font-weight: 900; font-style: italic; font-size: 24px; line-height: 26px; color: var(--ink); letter-spacing: 0.5px; }
</style>
</head>
<body>
<main class="flyer">
  <h1 class="abs title">REAL ESTATE<br>CAREER COURSE</h1>

  <p class="abs tagline tag-1">How to Make Money In Real Estate?</p>
  <p class="abs tagline tag-2">For those who have started or would like to go into Real Estate.</p>
  <p class="abs tagline tag-3">An investment in knowledge opens up untold opportunities.</p>

  <div class="abs houses-photo" role="img" aria-label="Rows of small white model houses with one red house standing out"></div>

  <section class="abs promo-panel" aria-label="Course format"></section>
  <div class="abs remote-illustration" role="img" aria-label="Illustration of a man in a light blue shirt watching a presenter on a laptop screen"></div>
  <div class="abs remote">REMOTE</div>
  <div class="abs sessions">SESSIONS</div>
  <div class="abs divider"></div>
  <div class="abs count">12</div>
  <div class="abs count-unit">session<br>course</div>
  <div class="abs start-date">Classes starting<br>June 16</div>

  <h2 class="abs topics-heading">A partial listing of Topics</h2>
  <ul class="topic-list">
    <li class="topic" style="left:104px;top:882px"><svg viewBox="0 0 18 18"><rect x="1" y="3" width="14" height="14" fill="none" stroke="#c2b06b" stroke-width="1.3"/><path d="M4 9l4 4 9-11" fill="none" stroke="#c2b06b" stroke-width="1.3"/></svg>Single-family</li>
    <li class="topic" style="left:104px;top:913px"><svg viewBox="0 0 18 18"><rect x="1" y="3" width="14" height="14" fill="none" stroke="#c2b06b" stroke-width="1.3"/><path d="M4 9l4 4 9-11" fill="none" stroke="#c2b06b" stroke-width="1.3"/></svg>Multifamily</li>
    <li class="topic" style="left:104px;top:944px"><svg viewBox="0 0 18 18"><rect x="1" y="3" width="14" height="14" fill="none" stroke="#c2b06b" stroke-width="1.3"/><path d="M4 9l4 4 9-11" fill="none" stroke="#c2b06b" stroke-width="1.3"/></svg>Management</li>
    <li class="topic" style="left:104px;top:975px"><svg viewBox="0 0 18 18"><rect x="1" y="3" width="14" height="14" fill="none" stroke="#c2b06b" stroke-width="1.3"/><path d="M4 9l4 4 9-11" fill="none" stroke="#c2b06b" stroke-width="1.3"/></svg>Real Estate Concepts</li>
    <li class="topic" style="left:104px;top:1006px"><svg viewBox="0 0 18 18"><rect x="1" y="3" width="14" height="14" fill="none" stroke="#c2b06b" stroke-width="1.3"/><path d="M4 9l4 4 9-11" fill="none" stroke="#c2b06b" stroke-width="1.3"/></svg>Real Estate law</li>

    <li class="topic" style="left:344px;top:882px"><svg viewBox="0 0 18 18"><rect x="1" y="3" width="14" height="14" fill="none" stroke="#c2b06b" stroke-width="1.3"/><path d="M4 9l4 4 9-11" fill="none" stroke="#c2b06b" stroke-width="1.3"/></svg>Investment properties</li>
    <li class="topic" style="left:344px;top:913px"><svg viewBox="0 0 18 18"><rect x="1" y="3" width="14" height="14" fill="none" stroke="#c2b06b" stroke-width="1.3"/><path d="M4 9l4 4 9-11" fill="none" stroke="#c2b06b" stroke-width="1.3"/></svg>Foreclosures</li>
    <li class="topic" style="left:344px;top:944px"><svg viewBox="0 0 18 18"><rect x="1" y="3" width="14" height="14" fill="none" stroke="#c2b06b" stroke-width="1.3"/><path d="M4 9l4 4 9-11" fill="none" stroke="#c2b06b" stroke-width="1.3"/></svg>Rehab</li>
    <li class="topic" style="left:344px;top:975px"><svg viewBox="0 0 18 18"><rect x="1" y="3" width="14" height="14" fill="none" stroke="#c2b06b" stroke-width="1.3"/><path d="M4 9l4 4 9-11" fill="none" stroke="#c2b06b" stroke-width="1.3"/></svg>Foreclosures</li>
    <li class="topic" style="left:344px;top:1006px"><svg viewBox="0 0 18 18"><rect x="1" y="3" width="14" height="14" fill="none" stroke="#c2b06b" stroke-width="1.3"/><path d="M4 9l4 4 9-11" fill="none" stroke="#c2b06b" stroke-width="1.3"/></svg>Short sales</li>

    <li class="topic" style="left:586px;top:882px"><svg viewBox="0 0 18 18"><rect x="1" y="3" width="14" height="14" fill="none" stroke="#c2b06b" stroke-width="1.3"/><path d="M4 9l4 4 9-11" fill="none" stroke="#c2b06b" stroke-width="1.3"/></svg>Development</li>
    <li class="topic" style="left:586px;top:913px"><svg viewBox="0 0 18 18"><rect x="1" y="3" width="14" height="14" fill="none" stroke="#c2b06b" stroke-width="1.3"/><path d="M4 9l4 4 9-11" fill="none" stroke="#c2b06b" stroke-width="1.3"/></svg>Finical modeling</li>
    <li class="topic" style="left:586px;top:944px"><svg viewBox="0 0 18 18"><rect x="1" y="3" width="14" height="14" fill="none" stroke="#c2b06b" stroke-width="1.3"/><path d="M4 9l4 4 9-11" fill="none" stroke="#c2b06b" stroke-width="1.3"/></svg>HUD properties</li>
    <li class="topic" style="left:586px;top:975px"><svg viewBox="0 0 18 18"><rect x="1" y="3" width="14" height="14" fill="none" stroke="#c2b06b" stroke-width="1.3"/><path d="M4 9l4 4 9-11" fill="none" stroke="#c2b06b" stroke-width="1.3"/></svg>&nbsp;Due Diligence e</li>
  </ul>

  <address class="abs company" style="font-style:normal">
    <div class="name">Company Name</div>
    <div>Address Line 01</div>
    <div>Address Line 02</div>
  </address>

  <ul class="abs contact">
    <li><svg viewBox="0 0 15 13"><path d="M1 5c0-3 13-3 13 0v1h-3V4.5H4V6H1z M3 7h9l2 5H1z" fill="#c2b06b"/></svg>+000 1234 5678</li>
    <li><svg viewBox="0 0 15 13"><rect x="0.5" y="1.5" width="14" height="10" fill="#c2b06b"/><path d="M0.5 1.5l7 6 7-6" fill="none" stroke="#fff" stroke-width="1.2"/></svg>hello@emailaddress.com</li>
    <li><svg viewBox="0 0 15 13"><rect x="1" y="1" width="13" height="8" fill="none" stroke="#c2b06b" stroke-width="1.4"/><path d="M7.5 9v3M4 12h7" stroke="#c2b06b" stroke-width="1.4"/></svg>www.website.com</li>
  </ul>

  <div class="abs hotline">
    <div class="label">HOTLINE</div>
    <div class="number">012345678911</div>
  </div>
</main>
</body>
</html>
```